Im open to ideas.. I was thinking on my business cards aswell as my logo. a place for my name. email. phone number and abn..

ive attched a file with my business logo. which i dont love the colours.. i was think a dark background with charcoal letters so something along those colour schumes but im open to ideas..

BRM Constructions

```html
<!DOCTYPE html>
<html lang="en">
<head>
<meta charset="utf-8">
<title>BRM Constructions – Business Card</title>
<link href="https://fonts.googleapis.com/css2?family=Open+Sans:wght@400;600;700&display=swap" rel="stylesheet">
<style>
  :root {
    --page: #e9e7e4;
    --card-black: #000000;
    --charcoal: #555555;
    --roof-grey: #7a7a7a;
    --brand-grey: #6a6a6a;
    --brand-dark: #333333;
    --text-light: #c9c9c9;
    --text-mid: #9a9a9a;
  }
  * { margin: 0; padding: 0; box-sizing: border-box; }
  html, body { width: 1200px; height: 900px; overflow: hidden; }
  body {
    position: relative;
    background: var(--page);
    font-family: "Open Sans", Arial, sans-serif;
  }
  .card {
    position: absolute;
    overflow: hidden;
    background: var(--card-black);
    box-shadow: 0 6px 18px rgba(0,0,0,0.25);
  }
  .card-front { left: 238px; top: 62px; width: 555px; height: 343px; }
  .card-back  { left: 457px; top: 518px; width: 560px; height: 343px; }

  .front-top {
    position: absolute; left: 0; top: 0; width: 100%; height: 168px;
    background: var(--charcoal);
  }
  .front-band {
    position: absolute; left: 0; top: 168px; width: 100%; height: 16px;
    background: var(--roof-grey);
  }
  .front-brand {
    position: absolute; right: 46px; top: 52px;
    font-weight: 700; font-size: 34px; letter-spacing: 1px;
    text-transform: uppercase; color: var(--brand-dark);
  }
  .abn {
    position: absolute; left: 44px; top: 192px;
    font-size: 14px; color: var(--text-mid);
  }
  .contact-list {
    position: absolute; left: 42px; top: 229px;
    list-style: none; font-size: 14px; color: var(--text-light);
  }
  .contact-list li { display: flex; align-items: center; height: 20px; }
  .contact-list svg { width: 12px; height: 12px; margin-right: 9px; fill: var(--text-mid); }
  .person {
    position: absolute; right: 47px; top: 245px; text-align: right;
  }
  .person-name { font-size: 17px; font-weight: 600; color: var(--text-mid); }
  .person-role { font-size: 14px; color: var(--text-light); margin-top: 1px; }
  .dash-rule {
    position: absolute; left: 0; top: 320px; width: 100%; height: 10px;
    background: repeating-linear-gradient(90deg, var(--roof-grey) 0 22px, transparent 22px 36px);
  }

  .back-brand {
    position: absolute; left: 0; right: 0; top: 150px; text-align: center;
    font-weight: 700; font-size: 38px; letter-spacing: 1px;
    text-transform: uppercase; color: var(--brand-grey);
  }
</style>
</head>
<body>
  <section class="card card-front">
    <div class="front-top"></div>
    <div class="front-band"></div>
    <div class="front-brand">BRM Constructions</div>

    <p class="abn">ABN : 12345678</p>
    <ul class="contact-list">
      <li><svg viewBox="0 0 24 24"><path d="M6.6 10.8a15.1 15.1 0 0 0 6.6 6.6l2.2-2.2a1 1 0 0 1 1-.25 11.4 11.4 0 0 0 3.6.57 1 1 0 0 1 1 1V20a1 1 0 0 1-1 1A17 17 0 0 1 3 4a1 1 0 0 1 1-1h3.5a1 1 0 0 1 1 1c0 1.25.2 2.45.57 3.57a1 1 0 0 1-.25 1z"/></svg>044-987 654 321</li>
      <li><svg viewBox="0 0 24 24"><path d="M2 5h20v14H2zm2 2v.5l8 5 8-5V7l-8 5z"/></svg>hello@brmbuild.com</li>
      <li><svg viewBox="0 0 24 24"><path d="M12 2a10 10 0 1 0 0 20 10 10 0 0 0 0-20zm6.9 9h-3a15 15 0 0 0-1.4-6A8 8 0 0 1 18.9 11zM12 4c.9 1.3 1.7 3.9 1.9 7h-3.8c.2-3.1 1-5.7 1.9-7zM9.5 5a15 15 0 0 0-1.4 6h-3A8 8 0 0 1 9.5 5zM5.1 13h3a15 15 0 0 0 1.4 6A8 8 0 0 1 5.1 13zm6.9 7c-.9-1.3-1.7-3.9-1.9-7h3.8c-.2 3.1-1 5.7-1.9 7zm2.5-1a15 15 0 0 0 1.4-6h3a8 8 0 0 1-4.4 6z"/></svg>www.brmbuild.com</li>
    </ul>
    <div class="person">
      <p class="person-name">Daniel Hart</p>
      <p class="person-role">Managing Director</p>
    </div>
    <div class="dash-rule"></div>
  </section>

  <section class="card card-back">
    <div class="back-brand">BRM Constructions</div>
  </section>
</body>
</html>
```